Web design required

1-We need a web design for existing company based in New Zealand
2-We build residential house and light commercial
3-We has in-house designer which allow us can provide interior design
4-We modeling project before site construction, which enable both client and construction team to visually analysis whole project,

Target Market(s)

middle class residential house market
Ref: http://www.parvellbuilders.co.nz/

Industry/Entity Type

Construction Company

Number of Pages Required

1 page

Font styles to use
Sans Serif
Other font styles liked:
• Such as : Central Gothic or similar which has more design taste

Colors

Designer to choose colors to be used in the design.

Requirements
Must have
• Front sheet, contact information, sample project

```html
<!DOCTYPE html>
<html lang="en">
<head>
<meta charset="utf-8">
<title>Harbourline Homes</title>
<link href="https://fonts.googleapis.com/css2?family=Raleway:wght@500;600;700&family=Roboto:wght@400;500;700&display=swap" rel="stylesheet">
<style>
:root{
  --blue:#0a63ad;
  --blue-deep:#08579a;
  --dark:#2f3032;
  --darker:#262729;
  --ink:#4a4a4a;
  --grey:#5c5c5c;
  --white:#ffffff;
  --line:#b9c7d4;
}
*{box-sizing:border-box;margin:0;padding:0}
html,body{width:1200px;height:3422px;overflow:hidden}
body{position:relative;background:var(--white);font-family:"Roboto",sans-serif;color:var(--ink)}
.abs{position:absolute}
.heading{font-family:"Raleway",sans-serif;font-weight:700;color:var(--grey);letter-spacing:1px;display:flex;align-items:center;gap:28px}
.heading::before,.heading::after{content:"";width:34px;height:6px;border-top:2px solid var(--line);border-bottom:2px solid var(--line)}
.btn{position:absolute;display:flex;align-items:center;justify-content:center;font-size:18px;font-weight:500;letter-spacing:.5px}
.btn-blue{background:var(--blue);color:var(--white)}
.btn-white{background:var(--white);color:var(--blue)}
.read{color:var(--blue);font-size:14px;font-weight:500;margin-top:8px;display:block}

/* hero */
.hero{left:0;top:0;width:1200px;height:677px;background:linear-gradient(120deg,#3c7fb8 0%,#5f97c3 35%,#8fb4cf 60%,#c9d8e2 100%)}
.navbar{left:0;top:39px;width:1200px;height:114px;background:rgba(40,40,42,.92)}
.brand{left:80px;top:58px;height:76px;display:flex;align-items:center;gap:14px;color:var(--white);font-family:"Raleway",sans-serif;font-weight:700;font-size:24px;letter-spacing:3px}
.brand-mark{width:40px;height:40px;background:var(--blue)}
.nav{left:531px;top:75px;display:flex;height:44px;font-size:16px;color:var(--white);font-weight:500}
.nav span{display:flex;align-items:center;padding:0 21px}
.nav .active{background:var(--blue)}
.hero-title{left:0;top:354px;width:1200px;text-align:center;font-family:"Raleway",sans-serif;font-weight:700;font-size:46px;color:var(--white);letter-spacing:1px;text-shadow:0 2px 6px rgba(0,0,0,.35)}

/* about */
.about-head{left:0;top:712px;width:1200px;justify-content:center;font-size:42px}
.about-text{left:250px;top:775px;width:708px;text-align:center;font-size:15px;line-height:26px;color:#333}
.about-text p+p{margin-top:4px}
.feature-img{position:absolute;height:208px}
.feature{position:absolute;width:180px}
.feature h3{font-family:"Raleway",sans-serif;font-weight:500;font-size:21px;color:var(--grey);margin-bottom:10px;white-space:nowrap}
.feature p{font-size:14px;line-height:24px;color:#444}
.feature.right{text-align:right}

/* banner */
.banner{left:0;top:1437px;width:1200px;height:240px;background:linear-gradient(90deg,#1f2224 0%,#3b3e40 50%,#2a2c2e 100%)}
.banner-text{left:0;top:1490px;width:1200px;text-align:center;font-family:"Raleway",sans-serif;font-weight:700;font-size:30px;line-height:39px;color:var(--white)}

/* services */
.worker{left:91px;top:1711px;width:331px;height:415px;background:radial-gradient(ellipse at 50% 45%,#3b4f8c 0%,#2b3a6c 45%,rgba(255,255,255,0) 72%)}
.services-head{left:486px;top:1736px;font-size:42px}
.services-head::before{display:none}
.service{position:absolute;width:300px;padding-left:68px}
.service svg{position:absolute;left:0;top:10px}
.service h4{font-size:19px;font-weight:500;color:#333;margin-bottom:6px}
.service p{font-size:14px;line-height:24px;color:#444}

/* projects */
.projects{left:0;top:2126px;width:1200px;height:417px;background:var(--blue-deep)}
.projects-head{left:0;top:2163px;width:1200px;justify-content:center;font-size:42px;color:var(--white)}
.projects-head::before,.projects-head::after{border-color:#9cc0e0}
.card{position:absolute;top:2235px;height:231px}
.arrow{position:absolute;top:2340px;width:26px;height:26px;background:var(--dark);display:flex;align-items:center;justify-content:center}

/* news */
.news-head{left:0;top:2578px;width:1200px;justify-content:center;font-size:42px}
.news-img{position:absolute;top:2650px;width:333px;height:208px}
.news{position:absolute;top:2870px;width:333px}
.news h5{font-size:17px;font-weight:400;line-height:28px;color:var(--blue)}
.news .date{display:flex;align-items:center;gap:8px;font-size:14px;color:#333;margin:8px 0 6px}
.news p{font-size:14px;line-height:24px;color:#444}
.news p b{color:var(--blue)}

/* footer */
.footer{left:0;top:3057px;width:1200px;height:310px;background:var(--dark)}
.footer h6{position:absolute;font-family:"Raleway",sans-serif;font-weight:500;font-size:30px;color:var(--white)}
.avatar{position:absolute;left:80px;width:90px;height:90px;border-radius:50%;border:3px solid var(--white);background:linear-gradient(160deg,#d9d4cf,#6e6a66)}
.quote{position:absolute;left:180px;width:280px;font-size:14px;line-height:24px;color:var(--white)}
.quote b{font-weight:700}
.contact-line{position:absolute;left:712px;font-size:15px;line-height:26px;color:var(--white)}
.copyright{left:0;top:3367px;width:1200px;height:55px;background:var(--blue);display:flex;align-items:center;justify-content:center;color:var(--white);font-size:15px}
</style>
</head>
<body>

<!-- hero -->
<div class="abs hero" role="img" aria-label="Photograph of two builders in hard hats reviewing house plans on site"></div>
<div class="abs navbar"></div>
<div class="abs brand"><span class="brand-mark"></span>HARBOURLINE HOMES</div>
<nav class="abs nav">
  <span class="active">HOME</span><span>ABOUT</span><span>SERVICES</span><span>PROJECTS</span><span>NEWS</span><span>CONTACT</span>
</nav>
<h1 class="abs hero-title">DESIGN YOUR DREAMS WITH US</h1>
<div class="btn btn-blue" style="left:417px;top:438px;width:169px;height:46px">CONTACT US</div>
<div class="btn btn-white" style="left:604px;top:438px;width:176px;height:46px">VIEW PROJECTS</div>

<!-- about -->
<h2 class="abs heading about-head">ABOUT US</h2>
<div class="abs about-text">
  <p>Lorem Ipsum is simply dummy text of the printing and typesetting industry. Lorem Ipsum has been the industry's standard dummy text ever since the 1500s, when an unknown printer took a galley of type and scrambled it to make a type specimen book.</p>
  <p>Lorem Ipsum is simply dummy text of the printing and typesetting industry. Lorem Ipsum has been the industry's standard dummy text ever since the 1500s.</p>
</div>

<div class="feature-img" role="img" aria-label="Photograph of builders working on a roof frame" style="left:78px;top:958px;width:287px;background:linear-gradient(135deg,#7fa7c9,#8a6a45);clip-path:polygon(0 0,100% 0,88% 100%,0 100%)"></div>
<div class="feature" style="left:399px;top:1000px"><h3>Quality Work</h3><p>Lorem Ipsum is simply dummy the printing and typesetting industry.</p><span class="read">READ MORE</span></div>
<div class="feature-img" role="img" aria-label="Photograph of a site team in hard hats" style="left:600px;top:958px;width:262px;background:linear-gradient(135deg,#8a5a3a,#6f95b9);clip-path:polygon(0 0,90% 0,100% 50%,90% 100%,0 100%)"></div>
<div class="feature" style="left:916px;top:1000px"><h3>Trusted Worker</h3><p>Lorem Ipsum is simply dummy the printing and typesetting industry.</p><span class="read">READ MORE</span></div>

<div class="feature right" style="left:103px;top:1208px"><h3>Heavy Materials</h3><p>Lorem Ipsum is simply dummy the printing and typesetting industry.</p><span class="read">READ MORE</span></div>
<div class="feature-img" role="img" aria-label="Photograph of engineers inside a building under construction" style="left:308px;top:1166px;width:290px;background:linear-gradient(135deg,#c9ccd0,#7c7f84);clip-path:polygon(12% 0,100% 0,100% 100%,12% 100%,0 50%)"></div>
<div class="feature right" style="left:625px;top:1208px"><h3>Expert Engineer</h3><p>Lorem Ipsum is simply dummy the printing and typesetting industry.</p><span class="read">READ MORE</span></div>
<div class="feature-img" role="img" aria-label="Photograph of engineers in safety vests" style="left:833px;top:1166px;width:287px;background:linear-gradient(135deg,#d9a24a,#b9581f);clip-path:polygon(12% 0,100% 0,100% 100%,12% 100%,0 50%)"></div>

<!-- banner -->
<div class="abs banner" role="img" aria-label="Dark photograph of building plans and a hard hat"></div>
<p class="abs banner-text">to create a sustainable future through building<br>preservation green architecture, and smart design</p>
<div class="btn btn-blue" style="left:512px;top:1578px;width:175px;height:46px">CONTACT US</div>

<!-- services -->
<div class="abs worker" role="img" aria-label="Photograph of a smiling builder in a yellow hard hat with arms crossed"></div>
<h2 class="abs heading services-head">OUR SERVICES</h2>
<div class="service" style="left:486px;top:1828px">
  <svg width="50" height="48" viewBox="0 0 50 48"><path d="M25 2 2 22h7v24h12V32h8v14h12V22h7z" fill="var(--blue)"/></svg>
  <h4>Service 1</h4><p>Lorem Ipsum is simply dummy the printing and typesetting.</p><span class="read">READ MORE</span></div>
<div class="service" style="left:821px;top:1828px">
  <svg width="50" height="48" viewBox="0 0 50 48"><path d="M4 12h16v36H4zM22 2h24v46H22z" fill="var(--blue)"/><g fill="#fff"><rect x="8" y="18" width="4" height="4"/><rect x="14" y="18" width="4" height="4"/><rect x="8" y="28" width="4" height="4"/><rect x="14" y="28" width="4" height="4"/><rect x="27" y="8" width="5" height="5"/><rect x="36" y="8" width="5" height="5"/><rect x="27" y="18" width="5" height="5"/><rect x="36" y="18" width="5" height="5"/><rect x="27" y="28" width="5" height="5"/><rect x="36" y="28" width="5" height="5"/></g></svg>
  <h4>Service 2</h4><p>Lorem Ipsum is simply dummy the printing and typesetting.</p><span class="read">READ MORE</span></div>
<div class="service" style="left:486px;top:1974px">
  <svg width="50" height="48" viewBox="0 0 50 48"><path d="M25 2 2 22h7v24h12V32h8v14h12V22h7z" fill="var(--blue)"/></svg>
  <h4>Service 3</h4><p>Lorem Ipsum is simply dummy the printing and typesetting.</p><span class="read">READ MORE</span></div>
<div class="service" style="left:821px;top:1974px">
  <svg width="50" height="48" viewBox="0 0 50 48"><path d="M4 12h16v36H4zM22 2h24v46H22z" fill="var(--blue)"/><g fill="#fff"><rect x="8" y="18" width="4" height="4"/><rect x="14" y="18" width="4" height="4"/><rect x="8" y="28" width="4" height="4"/><rect x="14" y="28" width="4" height="4"/><rect x="27" y="8" width="5" height="5"/><rect x="36" y="8" width="5" height="5"/><rect x="27" y="18" width="5" height="5"/><rect x="36" y="18" width="5" height="5"/><rect x="27" y="28" width="5" height="5"/><rect x="36" y="28" width="5" height="5"/></g></svg>
  <h4>Service 4</h4><p>Lorem Ipsum is simply dummy the printing and typesetting.</p><span class="read">READ MORE</span></div>

<!-- projects -->
<div class="abs projects"></div>
<h2 class="abs heading projects-head">PROJECT</h2>
<div class="arrow" style="left:52px"><svg width="10" height="12" viewBox="0 0 10 12"><path d="M8 1 2 6l6 5" stroke="#fff" stroke-width="2" fill="none"/></svg></div>
<div class="arrow" style="left:1122px"><svg width="10" height="12" viewBox="0 0 10 12"><path d="M2 1l6 5-6 5" stroke="#fff" stroke-width="2" fill="none"/></svg></div>

<div class="card" role="img" aria-label="Photograph of a modern commercial building" style="left:96px;width:324px;background:linear-gradient(160deg,#6b6f73,#3e4246)">
  <div style="position:absolute;inset:0;background:rgba(30,30,32,.45)"></div>
  <div style="position:absolute;left:100px;top:60px;width:50px;height:50px;background:var(--white);display:flex;align-items:center;justify-content:center">
    <svg width="26" height="26" viewBox="0 0 26 26" fill="none" stroke="var(--blue)" stroke-width="3"><path d="M2 9V2h7M17 2h7v7M24 17v7h-7M9 24H2v-7"/><rect x="8" y="8" width="10" height="10"/></svg>
  </div>
  <div style="position:absolute;left:158px;top:60px;width:50px;height:50px;background:var(--blue);display:flex;align-items:center;justify-content:center">
    <svg width="20" height="22" viewBox="0 0 20 22"><path d="M3 2l15 9-15 9z" fill="#fff"/></svg>
  </div>
  <div style="position:absolute;left:0;top:126px;width:100%;text-align:center;font-family:'Raleway',sans-serif;font-weight:700;font-size:32px;color:#fff">Project Name</div>
</div>
<div class="card" role="img" aria-label="Photograph of an interior with decorative screen panels" style="left:438px;width:326px;background:linear-gradient(160deg,#8a6a3e,#3a2e22 60%,#b7b2ab)"></div>
<div class="card" role="img" aria-label="Photograph of a finished brick family home" style="left:785px;width:323px;background:linear-gradient(180deg,#c9d9e6 0%,#c9d9e6 35%,#8a6450 55%,#5c7a3a 100%)"></div>

<!-- news -->
<h2 class="abs heading news-head">LATEST NEWS</h2>
<div class="news-img" role="img" aria-label="Photograph of engineers reviewing plans outdoors" style="left:78px;background:linear-gradient(160deg,#6aa5d8,#c8d6e0 60%,#8f7a5c)"></div>
<div class="news-img" role="img" aria-label="Photograph of a model house frame on drawings" style="left:433px;background:linear-gradient(160deg,#e8e6e2,#c99a5c 55%,#6f6f72)"></div>
<div class="news-img" role="img" aria-label="Photograph of builders on site with a tablet" style="left:789px;background:linear-gradient(160deg,#7fb2de,#a9c6dc 50%,#3f5f8e)"></div>

<div class="news" style="left:78px"><h5>Lorem Ipsum is simply dummy text of the printing</h5>
  <div class="date"><svg width="14" height="14" viewBox="0 0 14 14"><rect x="1" y="2" width="12" height="11" fill="none" stroke="#333" stroke-width="1.5"/><path d="M1 5h12M4 0v3M10 0v3" stroke="#333" stroke-width="1.5"/></svg>12th April 2016</div>
  <p>Lorem Ipsum is simply dummy text of the printing and typesetting industry... <b>»</b></p></div>
<div class="news" style="left:433px"><h5>Lorem Ipsum is simply dummy text of the printing</h5>
  <div class="date"><svg width="14" height="14" viewBox="0 0 14 14"><rect x="1" y="2" width="12" height="11" fill="none" stroke="#333" stroke-width="1.5"/><path d="M1 5h12M4 0v3M10 0v3" stroke="#333" stroke-width="1.5"/></svg>12th April 2016</div>
  <p>Lorem Ipsum is simply dummy text of the printing and typesetting industry... <b>»</b></p></div>
<div class="news" style="left:789px"><h5>Lorem Ipsum is simply dummy text of the printing</h5>
  <div class="date"><svg width="14" height="14" viewBox="0 0 14 14"><rect x="1" y="2" width="12" height="11" fill="none" stroke="#333" stroke-width="1.5"/><path d="M1 5h12M4 0v3M10 0v3" stroke="#333" stroke-width="1.5"/></svg>12th April 2016</div>
  <p>Lorem Ipsum is simply dummy text of the printing and typesetting industry... <b>»</b></p></div>

<!-- footer -->
<footer class="abs footer">
  <h6 style="left:80px;top:33px">Testimonials</h6>
  <div class="avatar" role="img" aria-label="Client portrait photograph" style="top:87px"></div>
  <p class="quote" style="top:99px">There are many variations of passages of Lorem Ipsum available..<br><b>-Client Name</b></p>
  <div class="avatar" role="img" aria-label="Client portrait photograph" style="top:190px"></div>
  <p class="quote" style="top:202px">There are many variations of passages of Lorem Ipsum available..<br><b>-Client Name</b></p>

  <h6 style="left:632px;top:33px">Contact info</h6>
  <svg class="abs" style="left:627px;top:84px" width="66" height="74" viewBox="0 0 66 74"><path d="M33 2 63 19v36L33 72 3 55V19z" fill="none" stroke="#5a6a7a" stroke-width="2"/><path d="M33 20v36M22 28h22l4 4-4 4H22zM44 40H22l-4 4 4 4h22z" fill="none" stroke="#fff" stroke-width="3"/></svg>
  <p class="contact-line" style="top:99px">street area city, state<br>country.</p>
  <svg class="abs" style="left:627px;top:192px" width="66" height="74" viewBox="0 0 66 74"><path d="M33 2 63 19v36L33 72 3 55V19z" fill="none" stroke="#5a6a7a" stroke-width="2"/><path d="M24 23c2-2 4-2 5 0l3 5c1 2 0 3-2 4 1 4 4 7 8 8 1-2 2-3 4-2l5 3c2 1 2 3 0 5-3 3-7 3-11 1-6-3-10-8-13-14-1-4-1-8 1-10z" fill="#fff"/></svg>
  <p class="contact-line" style="top:200px">Phone No. : 123 456 7890<br>Email : info@harbourlinehomes.co.nz</p>
</footer>
<div class="abs copyright">2017 ©HARBOURLINE HOMES. - All Rights Reserved.</div>

</body>
</html>
```